TA BRAMLEY BUSINESS CARD DESIGN PROJECT

We need to utilize our logo that was expertly created on PixelHarbor and now need to match this with a business card design.

```html
<!DOCTYPE html>
<html lang="en">
<head>
<meta charset="utf-8">
<title>TA Bramley Business Card</title>
<link href="https://fonts.googleapis.com/css2?family=Montserrat:wght@400;500;700&display=swap" rel="stylesheet">
<style>
  :root {
    --page-bg: #e9e6e1;
    --card-dark: #1f2022;
    --card-dark-edge: #2a2b2e;
    --brand-blue: #1d5fa8;
    --brand-blue-deep: #0f3d73;
    --name-blue: #1e4f8e;
    --text-gold: #d9c9a6;
  }
  html, body {
    margin: 0;
    padding: 0;
    width: 1200px;
    height: 1047px;
    overflow: hidden;
    background: var(--page-bg);
  }
  .stage {
    position: relative;
    width: 1200px;
    height: 1047px;
  }
  .business-card {
    position: absolute;
    left: 120px;
    top: 263px;
    width: 960px;
    height: 520px;
    border-radius: 22px;
    overflow: hidden;
    background: radial-gradient(ellipse at 40% 50%, var(--card-dark-edge), var(--card-dark) 70%);
    box-shadow: 0 18px 40px rgba(0,0,0,0.18);
    font-family: "Montserrat", sans-serif;
  }
  .card-curves {
    position: absolute;
    inset: 0;
  }
  .brand-name {
    position: absolute;
    left: 40px;
    width: 440px;
    top: 228px;
    text-align: center;
    font-size: 46px;
    font-weight: 700;
    letter-spacing: 4px;
    color: var(--brand-blue);
  }
  .divider {
    position: absolute;
    left: 520px;
    top: 120px;
    width: 3px;
    height: 284px;
    background: var(--brand-blue);
  }
  .contact-block {
    position: absolute;
    left: 560px;
    top: 114px;
    color: var(--text-gold);
  }
  .person-name {
    margin: 0;
    font-size: 31px;
    font-weight: 700;
    letter-spacing: 1px;
    color: var(--name-blue);
  }
  .person-title {
    margin: 2px 0 0;
    font-size: 23px;
    font-weight: 500;
  }
  .contact-list {
    list-style: none;
    margin: 22px 0 0;
    padding: 0;
  }
  .contact-list li {
    display: flex;
    align-items: center;
    gap: 8px;
    font-size: 23px;
    line-height: 31px;
  }
  .contact-list svg {
    width: 20px;
    height: 18px;
    fill: var(--text-gold);
    flex: none;
  }
  .address {
    margin: 20px 0 0;
    font-size: 23px;
    line-height: 31px;
  }
</style>
</head>
<body>
<div class="stage">
  <div class="business-card">
    <svg class="card-curves" viewBox="0 0 960 520" preserveAspectRatio="none" aria-hidden="true">
      <defs>
        <linearGradient id="curveBlue" x1="0" y1="0" x2="1" y2="1">
          <stop offset="0" stop-color="#1d5fa8"/>
          <stop offset="1" stop-color="#0f3d73"/>
        </linearGradient>
      </defs>
      <path d="M0,0 H250 Q70,70 0,258 Z" fill="url(#curveBlue)"/>
      <path d="M960,272 Q890,470 700,520 H960 Z" fill="url(#curveBlue)"/>
    </svg>

    <div class="brand-name">TA BRAMLEY</div>

    <div class="divider"></div>

    <div class="contact-block">
      <h1 class="person-name">DANIEL HARTWELL</h1>
      <p class="person-title">Managing Director</p>
      <ul class="contact-list">
        <li>
          <svg viewBox="0 0 20 18"><path d="M2 5 Q10 0 18 5 L16 8 L13 7 L13 5 Q10 4 7 5 L7 7 L4 8 Z M5 9 H15 L17 16 H3 Z"/></svg>
          123 456 789
        </li>
        <li>
          <svg viewBox="0 0 20 18"><rect x="5" y="1" width="10" height="6"/><rect x="2" y="7" width="16" height="10" rx="1"/></svg>
          123 456 789
        </li>
        <li>
          <svg viewBox="0 0 20 18"><path d="M2 4 H18 V15 H2 Z M2 4 L10 10 L18 4" /></svg>
          info@yourmail.com
        </li>
        <li>
          <svg viewBox="0 0 20 18"><circle cx="10" cy="9" r="8"/></svg>
          www.yourwebsite.com
        </li>
      </ul>
      <p class="address">Your address, City<br>State, Zip 1234</p>
    </div>
  </div>
</div>
</body>
</html>
```